2 Flow Charts showing Fair Trade vs Market Trade****See new image*****

I am starting a coffee roasting company where I warehouse coffee for farmers I met in Nicaragua as a Harbor League Volunteer.

I need one flow chart to show the normal path of coffee, from the producer to the exporter, to the importer, to the roaster, and ultimately to the consumer, each of which taking a little along the way, leaving the farmer less.

Then another flow chart showing a close relationship between my company (Brass Lantern Coffee) and the producer, with out the exporter/importer, and more money going to the farmer.

I have included my attempt at the flow charts, which look clunky and are in super low res.

You can see how I want to use the flow charts in the following website:

brasslanterncoffeeroasters.example

****** Just reduced the verbiage on the Flow Charts****************
***************See new image*******************************

Target Market(s)

Coffee consumers interested in fair trade.

Industry/Entity Type

It Company

Font styles to use
Sans Serif

Requirements
Must have
• Originally thinking black and white, but am open to color.
Nice to have
• Would like to see a design in both color and monochrome. I am having a difficult time determining which would look better on the site.

```html
<!DOCTYPE html>
<html lang="en">
<head>
<meta charset="utf-8">
<title>The Brass Lantern Model</title>
<link href="https://fonts.googleapis.com/css2?family=Jost:wght@400;500;700;800;900&display=swap" rel="stylesheet">
<style>
  :root {
    --ink: #111111;
    --paper: #ffffff;
  }
  html, body {
    margin: 0;
    padding: 0;
    width: 1200px;
    height: 1000px;
    overflow: hidden;
    background: var(--paper);
  }
  .canvas {
    position: relative;
    width: 1200px;
    height: 1000px;
    font-family: "Jost", "Futura", sans-serif;
    color: var(--ink);
  }
  .model-title {
    position: absolute;
    top: 308px;
    left: 0;
    width: 1200px;
    margin: 0;
    text-align: center;
    font-size: 38px;
    font-weight: 900;
    letter-spacing: 0;
    line-height: 1;
  }
  .model-tagline {
    position: absolute;
    top: 360px;
    left: 0;
    width: 1200px;
    margin: 0;
    text-align: center;
    font-size: 16px;
    font-weight: 700;
    line-height: 30px;
  }
  .model-tagline span {
    position: relative;
    display: inline-block;
    padding: 0 10px;
  }
  .model-tagline span::before,
  .model-tagline span::after {
    content: "";
    position: absolute;
    top: 0;
    width: 5px;
    height: 26px;
    border: 2px solid var(--ink);
  }
  .model-tagline span::before { left: 0; border-right: none; }
  .model-tagline span::after { right: 0; border-left: none; }
  .flow {
    position: absolute;
    top: 0;
    left: 0;
  }
  .flow .line { fill: none; stroke: var(--ink); stroke-width: 2; }
  .flow .node circle { fill: var(--paper); stroke: var(--ink); stroke-width: 2; }
  .flow .node text { font-size: 10px; font-weight: 800; text-anchor: middle; dominant-baseline: central; }
  .flow .label { font-size: 10.5px; font-weight: 800; text-anchor: middle; }
  .flow .money { font-size: 14px; font-weight: 800; }
  .flow .money-lg { font-size: 22px; font-weight: 900; }
  .flow .note { font-size: 14.5px; font-weight: 500; }
  .flow .note.strong { font-weight: 700; }
  .flow .cup-title { font-size: 18px; font-weight: 800; }
  .flow .cup-note { font-size: 16px; font-weight: 500; }
  .flow .cup-note.strong { font-weight: 700; }
  .flow .solid { fill: var(--ink); }
  .flow .outline { fill: none; stroke: var(--ink); stroke-width: 2.5; stroke-linejoin: round; }
  .flow .vs-text { font-size: 15px; font-weight: 900; font-style: italic; text-anchor: middle; }
</style>
</head>
<body>
<div class="canvas">
  <h1 class="model-title">THE BRASS LANTERN MODEL</h1>
  <p class="model-tagline"><span>We do things differently. We do away with the middlemen and give more to the farmers.</span></p>

  <svg class="flow" width="1200" height="1000" viewBox="0 0 1200 1000">
    <defs>
      <marker id="arrowhead" markerUnits="userSpaceOnUse" markerWidth="8" markerHeight="9" refX="7" refY="4.5" orient="auto">
        <path d="M1,1 L7,4.5 L1,8" fill="none" stroke="#111" stroke-width="1.6"/>
      </marker>
      <g id="bean">
        <ellipse cx="0" cy="0" rx="3.5" ry="5" fill="#111" transform="rotate(35)"/>
        <path d="M-1.5,2.5 Q0.5,0 1.5,-2.5" stroke="#fff" stroke-width="1" fill="none"/>
      </g>
    </defs>

    <!-- Traditional chain -->
    <g class="chain-traditional">
      <rect x="57" y="414" width="24" height="42" rx="4" class="solid" role="img" aria-label="Farmer icon"/>
      <g class="icon-exporter">
        <path class="outline" d="M230,460 V442 A17,17 0 0 1 264,442 V460 Z"/>
        <path class="outline" d="M240,428 A17,17 0 0 1 274,442 V460 H264"/>
        <rect x="240" y="447" width="14" height="13" class="outline"/>
        <path class="outline" d="M240,452 H254 M240,456 H254"/>
      </g>
      <g class="icon-importer">
        <path class="outline" d="M420,460 V440 L432,430 L446,440 V460 H436 V448 H428 V460 Z"/>
      </g>
      <g class="icon-roaster">
        <path class="outline" d="M409,588 L432,568 L455,588 M414,584 V607 H450 V584"/>
        <rect x="427" y="592" width="10" height="15" class="outline"/>
      </g>
      <g class="icon-cup">
        <path class="outline" d="M240,588 H268 V600 A10,10 0 0 1 258,608 H250 A10,10 0 0 1 240,598 Z"/>
        <path class="outline" d="M268,592 H274 A4,4 0 0 1 274,601 H267"/>
        <path d="M252,578 q-3,-4 0,-8 M257,578 q-3,-4 0,-8" stroke="#111" stroke-width="1.5" fill="none"/>
        <use href="#bean" x="254" y="597"/>
      </g>

      <text class="label" x="69" y="476">PRODUCER</text>
      <text class="label" x="251" y="476">EXPORTER</text>
      <text class="label" x="433" y="476">IMPORTER</text>
      <text class="label" x="255" y="623">YOUR COFFEE</text>
      <text class="label" x="433" y="623">COFFEE ROASTER</text>

      <!-- money flows -->
      <path class="line" d="M125,472 H112" marker-end="url(#arrowhead)"/>
      <text class="money" x="128" y="477">$</text>
      <path class="line" d="M140,472 H210"/>
      <path class="line" d="M306,472 H293" marker-end="url(#arrowhead)"/>
      <text class="money" x="309" y="477">$$</text>
      <path class="line" d="M332,472 H392"/>
      <path class="line" d="M486,472 H473" marker-end="url(#arrowhead)"/>
      <text class="money" x="489" y="477">$$$</text>
      <path class="line" d="M518,472 H528 V621 H484"/>
      <path class="line" d="M300,620 H324"/>
      <text class="money" x="328" y="625">$$$$</text>
      <path class="line" d="M366,620 H380" marker-end="url(#arrowhead)"/>

      <!-- goods line -->
      <path class="line" d="M42,489 H515 V636 H262"/>
      <path class="line" d="M69,497 V507 H92"/>
      <use href="#bean" x="100" y="507"/>
      <path class="line" d="M108,507 H130" marker-end="url(#arrowhead)"/>
      <path class="line" d="M251,497 V507 H274"/>
      <use href="#bean" x="282" y="507"/>
      <path class="line" d="M290,507 H312" marker-end="url(#arrowhead)"/>
      <path class="line" d="M433,497 V532"/>
      <use href="#bean" x="433" y="545"/>
      <path class="line" d="M433,553 V565" marker-end="url(#arrowhead)"/>

      <path class="line" d="M433,644 V660 H353"/>
      <use href="#bean" x="345" y="660"/>
      <path class="line" d="M337,660 H42 V626" marker-end="url(#arrowhead)"/>

      <g class="node"><circle cx="69" cy="489" r="8"/><text x="69" y="489">1</text></g>
      <g class="node"><circle cx="251" cy="489" r="8"/><text x="251" y="489">2</text></g>
      <g class="node"><circle cx="433" cy="489" r="8"/><text x="433" y="489">3</text></g>
      <g class="node"><circle cx="433" cy="636" r="8"/><text x="433" y="636">4</text></g>
      <g class="node"><circle cx="254" cy="636" r="8"/><text x="254" y="636">5</text></g>

      <text class="note" x="38" y="582">Traditionally, farmers</text>
      <text class="note" x="38" y="600">sell their coffee for</text>
      <text class="note strong" x="38" y="618">1$ to $1.85 a pound</text>
    </g>

    <!-- VS mark -->
    <g class="versus">
      <path class="line" d="M579,520 L622,593 M622,520 L579,593"/>
      <rect x="582" y="545" width="37" height="23" fill="#fff" stroke="#111" stroke-width="2"/>
      <text class="vs-text" x="600" y="562">VS</text>
    </g>

    <!-- Direct chain -->
    <g class="chain-direct">
      <rect x="740" y="414" width="24" height="42" rx="4" class="solid" role="img" aria-label="Farmer icon"/>
      <text class="label" x="752" y="476">PRODUCER</text>
      <text class="money" x="693" y="477">$</text>
      <path class="line" d="M704,472 H719" marker-end="url(#arrowhead)"/>
      <path class="line" d="M689,472 H680 V621 H702"/>
      <path class="line" d="M688,472 V636 H744"/>

      <path class="line" d="M752,497 V522"/>
      <use href="#bean" x="752" y="531"/>
      <path class="line" d="M752,539 V551" marker-end="url(#arrowhead)"/>
      <rect class="solid company-mark" x="733" y="563" width="38" height="38"/>
      <text class="label" x="752" y="623">BRASS LANTERN</text>

      <g class="node"><circle cx="752" cy="489" r="8"/><text x="752" y="489">1</text></g>
      <g class="node"><circle cx="752" cy="636" r="8"/><text x="752" y="636">1</text></g>

      <text class="money-lg" x="942" y="497">$$</text>
      <path class="line" d="M938,489 H762" marker-end="url(#arrowhead)"/>
      <text class="money-lg" x="942" y="644">$$</text>
      <path class="line" d="M938,636 H762" marker-end="url(#arrowhead)"/>
      <path class="line" d="M976,489 H1003 V636 H976"/>
      <g class="node"><circle cx="1003" cy="563" r="8"/><text x="1003" y="563">2</text></g>

      <g class="icon-cup-large">
        <path class="solid" d="M1060,468 H1116 V492 A20,20 0 0 1 1096,512 H1080 A20,20 0 0 1 1060,492 Z"/>
        <path class="outline" d="M1116,474 H1124 A9,9 0 0 1 1124,492 H1114"/>
        <path d="M1084,458 q-4,-5 0,-10 M1092,458 q-4,-5 0,-10" stroke="#111" stroke-width="2" fill="none"/>
        <ellipse cx="1088" cy="490" rx="7" ry="10" fill="#fff" transform="rotate(30 1088 490)"/>
        <path d="M1084,497 Q1089,490 1092,483" stroke="#111" stroke-width="2" fill="none"/>
      </g>
      <text class="cup-title" x="1025" y="541">YOUR COFFEE</text>
      <text class="cup-note" x="1025" y="565">We share revenues,</text>
      <text class="cup-note" x="1025" y="587">guaranteeing</text>
      <text class="cup-note" x="1025" y="609">our farmers</text>
      <text class="cup-note strong" x="1025" y="631">$3.25 a pound</text>
    </g>
  </svg>
</div>
</body>
</html>
```